Corvane Lending Partners. Professional and Established Company

A full service finance company specializing in obtaining capital for small business. Business Lending advisor, helping small business owners access the capital they need to launch, grow, or sustain their business. Many of our programs offer flexible guidelines to overcome common obstacles such as credit score, credit history, and time in business, financials, and industry type. Our streamlined funding process makes getting a business loan, business line of credit, stated income commercial real estate loan, a smooth and stress free experience.SOME OF THE MOST COMMON NEEDS FOR BUSINESS CAPITAL:• Working Capital• Debt Consolidations (loans, merchant cash advances, etc.)• Payroll• Operating Expenses• Inventory• Equipment Financing• Commercial Real Estate (Purchase, Fix & Flip, Rehab, Renovations)• Business Acquisitions• Business ExpansionWe like the websites:www.quillmorecf.com they are in the same industry and provide the same servicesWe are wanting to be able to update when we do press releases and such using Word Press. Our look should be very professional and we will be adding Our Team Professional Bios and Headshots.

Industry/Entity Type

Finance

Number of Pages Required

5+ page

Font styles to use
Serif
Sans Serif

Requirements
Must have
• We want to copy quillmorecf.com
• We need:
• Home Page
• About Us
• Loan Programs
• Loan Criteria
• News
• Apply Now
• Contact
Nice to have
• See quillmorecf.com
Should not have
• Need professional design. Nothing bright or abstract

```html
<!DOCTYPE html>
<html lang="en">
<head>
<meta charset="utf-8">
<title>Corvane Lending Partners</title>
<link rel="stylesheet" href="https://fonts.googleapis.com/css2?family=Montserrat:wght@400;500;600;700&display=swap">
<style>
:root{
  --navy:#1f5aa6;
  --ink:#2c2f36;
  --muted:#8a8f99;
  --hero-a:#2b3746;
  --hero-b:#121a24;
  --services-a:#3a3d42;
  --services-b:#1e2024;
  --footer:#4f535a;
  --footer-dark:#3f4248;
  --white:#ffffff;
  --line:#d9dce2;
}
*{margin:0;padding:0;box-sizing:border-box}
html,body{width:1200px;height:3930px;overflow:hidden}
body{font-family:"Montserrat",sans-serif;color:var(--ink);background:var(--white);position:relative}
section,header,footer{position:absolute;left:0;width:1200px}
.abs{position:absolute}

/* hero */
.hero{top:0;height:676px;background:linear-gradient(135deg,#3b4859 0%,var(--hero-a) 40%,var(--hero-b) 100%)}
.hero-photo{position:absolute;inset:0;background:radial-gradient(ellipse at 70% 40%,rgba(120,140,165,.35),transparent 60%),radial-gradient(ellipse at 20% 80%,rgba(90,100,115,.4),transparent 55%)}
.topbar{top:0;height:63px;width:1200px;border-bottom:1px solid rgba(255,255,255,.18);color:#dfe4ea;font-size:13px}
.topbar .contact{left:90px;top:22px;display:flex;gap:40px}
.topbar .contact span{display:flex;align-items:center;gap:10px}
.topbar .social{right:90px;top:22px;display:flex;gap:14px}
.dot{width:12px;height:12px;border-radius:50%;background:#dfe4ea}
.brand{left:90px;top:82px;color:var(--white);font-weight:600;font-size:24px;letter-spacing:1px;line-height:1.2}
.brand small{display:block;font-size:12px;letter-spacing:3px;font-weight:500}
.nav{right:90px;top:100px;display:flex;color:var(--white);font-size:16px}
.nav span{padding:0 15px;border-left:1px solid rgba(255,255,255,.7);line-height:16px}
.nav span:first-child{border-left:0}
.hero-title{top:312px;width:1200px;text-align:center;color:var(--white);font-size:44px;font-weight:500;letter-spacing:1px}
.hero-title b{font-weight:700}
.hero-text{top:384px;left:130px;width:940px;text-align:center;color:#e6eaef;font-size:20px;line-height:40px}
.btn{display:flex;align-items:center;justify-content:center;gap:10px;border:3px solid var(--white);border-radius:30px;color:var(--white);font-weight:700;font-size:17px}
.hero .btn{left:507px;top:484px;width:186px;height:54px}

/* news */
.news{top:676px;height:799px}
.sec-title{width:1200px;text-align:center;color:var(--navy);font-size:34px;font-weight:700;letter-spacing:1px}
.news .sec-title{top:77px}
.photo{background:linear-gradient(135deg,#8a7c6f,#3e4650)}
.photo-frame{border:4px solid var(--white);position:absolute}
.news-img{width:460px;height:255px;box-shadow:0 2px 8px rgba(0,0,0,.2)}
.news-card{width:460px;height:255px;border:1px solid var(--line);padding:30px 24px;background:var(--white)}
.news-card h3{color:var(--navy);font-size:15px;font-weight:600;margin-bottom:14px}
.news-card p{color:var(--muted);font-size:11px;line-height:20px}
.meta{display:flex;gap:22px;margin-top:14px;font-size:11px;color:var(--navy);font-weight:600}

/* services */
.services{top:1475px;height:935px;background:linear-gradient(160deg,var(--services-a),var(--services-b))}
.services .sec-title{top:56px;color:var(--white)}
.services .lead{top:112px;left:260px;width:680px;text-align:center;color:#e2e5ea;font-size:15px;line-height:26px}
.svc{width:325px;height:285px;border:1px solid rgba(255,255,255,.55);background:linear-gradient(150deg,#6f7b88,#2c333c);color:var(--white);text-align:center;padding-top:82px}
.svc h4{font-size:16px;font-weight:700;margin-bottom:14px;letter-spacing:.5px}
.svc p{font-size:15px;line-height:26px;padding:0 42px;color:#eef1f4}
.services .btn{left:498px;top:812px;width:204px;height:53px}

/* team */
.team{top:2410px;height:624px}
.team .sec-title{top:82px}
.member{top:158px;width:441px;height:340px;background:var(--white);box-shadow:0 2px 10px rgba(0,0,0,.2)}
.member .portrait{position:absolute;top:0;width:213px;height:340px;background:linear-gradient(160deg,#c9ccd1,#6b7380)}
.member .bio{position:absolute;top:42px;width:200px}
.bio h3{font-size:28px;font-weight:500;color:var(--navy);line-height:38px}
.bio h5{font-size:15px;font-weight:700;margin-top:20px;line-height:22px}
.bio p{font-size:15px;line-height:26px;margin-top:22px}
.bio .icons{display:flex;gap:12px;margin-top:20px}
.bio .icons i{width:10px;height:10px;border-radius:50%;background:var(--navy)}
.arrow{width:34px;height:34px;border:2px solid #555;border-radius:50%;top:312px}

/* video */
.video{top:3034px;height:482px;background:linear-gradient(160deg,#6d7885,#3a4350 60%,#2a313b)}
.play{left:574px;top:133px}
.video .label{top:200px;width:1200px;text-align:center;color:var(--white);font-size:24px}
.video h2{top:240px;width:1200px;text-align:center;color:var(--white);font-size:36px;font-weight:700}
.video p{top:302px;left:200px;width:800px;text-align:center;color:#e6e9ed;font-size:16px;line-height:34px}

/* footer */
.footer{top:3516px;height:348px;background:var(--footer)}
.footer .brand{left:97px;top:170px;font-size:20px}
.footer .brand small{font-size:10px}
.f-social{left:112px;top:247px;display:flex;gap:10px}
.f-social i{width:22px;height:22px;border-radius:50%;background:var(--white)}
.footer h4{color:var(--white);font-size:26px;font-weight:600}
.footer ul{list-style:none;margin-top:30px}
.footer li{color:#eceef1;font-size:13px;line-height:27px;display:flex;align-items:center;gap:16px}
.footer li::before{content:"";width:8px;height:8px;border-radius:50%;background:var(--white)}
.contact-list{margin-top:30px;color:#eceef1;font-size:13px}
.contact-list div{display:flex;gap:22px;margin-bottom:16px;line-height:20px}
.copyright{top:3864px;height:66px;background:var(--footer-dark);color:#e6e8eb;font-size:13px;text-align:center;line-height:66px}
</style>
</head>
<body>

<header class="hero">
  <div class="hero-photo" role="img" aria-label="Photo of stacked coins and a financial city skyline with rising bar charts"></div>
  <div class="topbar abs">
    <div class="contact abs">
      <span><svg width="12" height="12" viewBox="0 0 24 24"><path fill="#dfe4ea" d="M6.6 10.8a15 15 0 006.6 6.6l2.2-2.2c.3-.3.7-.4 1-.2 1.1.4 2.3.6 3.6.6.6 0 1 .4 1 1V20c0 .6-.4 1-1 1A17 17 0 013 4c0-.6.4-1 1-1h3.5c.6 0 1 .4 1 1 0 1.3.2 2.5.6 3.6.1.3 0 .7-.2 1z"/></svg>888 888 8888</span>
      <span><svg width="14" height="11" viewBox="0 0 24 18"><rect x="1" y="1" width="22" height="16" fill="none" stroke="#dfe4ea" stroke-width="2"/><path d="M1 1l11 9 11-9" fill="none" stroke="#dfe4ea" stroke-width="2"/></svg>info@corvane.com</span>
    </div>
    <div class="social abs"><i class="dot"></i><i class="dot"></i><i class="dot"></i><i class="dot"></i></div>
  </div>
  <div class="brand abs">CORVANE<small>LENDING PARTNERS</small></div>
  <nav class="nav abs"><span>Home</span><span>About</span><span>Loan Programs</span><span>Loan Criteria</span><span>News</span><span>Contact</span></nav>
  <h1 class="hero-title abs">WELCOME TO <b>CORVANE</b></h1>
  <p class="hero-text abs">Our streamlined funding process makes getting a business loan, business line of credit, stated income commercial real estate loan, a smooth and stress free experience.</p>
  <div class="btn abs"><svg width="18" height="18" viewBox="0 0 24 24"><path fill="#fff" d="M22 2L2 10l8 3 3 8z"/></svg>APPLY NOW</div>
</header>

<section class="news">
  <h2 class="sec-title abs">RECENT NEWS</h2>
  <div class="news-img photo abs" style="left:131px;top:160px" role="img" aria-label="Photo of a couple reviewing documents at a laptop">
    <div class="photo-frame" style="left:30px;top:14px;right:14px;bottom:14px"></div>
  </div>
  <article class="news-card abs" style="left:608px;top:160px">
    <h3>AT VERO EOS ET ACCUSAMUS ET IUSTO ODIO</h3>
    <p>Sed ut perspiciatis unde omnis iste natus error sit voluptatem accusantium doloremque laudantium, totam rem aperiam, eaque ipsa quae ab illo inventore veritatis et quasi architecto beatae vitae dicta sunt explicabo. Nemo enim ipsam voluptatem quia voluptas sit aspernatur aut odit aut fugit, sed quia consequuntur magni dolores eos qui ratione voluptatem sequi nesciunt.</p>
    <div class="meta"><span>READ MORE →</span><span>▦ 04 November 2018</span><span>◷ 2 hrs ago</span></div>
  </article>
  <article class="news-card abs" style="left:131px;top:454px">
    <h3>LOREM IPSUM DOLOR SIT, CONSECTETUR</h3>
    <p>Sed ut perspiciatis unde omnis iste natus error sit voluptatem accusantium doloremque laudantium, totam rem aperiam, eaque ipsa quae ab illo inventore veritatis et quasi architecto beatae vitae dicta sunt explicabo. Nemo enim ipsam voluptatem quia voluptas sit aspernatur aut odit aut fugit, sed quia consequuntur magni dolores eos qui ratione voluptatem sequi nesciunt.</p>
    <div class="meta"><span>READ MORE →</span><span>▦ 04 November 2018</span><span>◷ 2 hrs ago</span></div>
  </article>
  <div class="news-img photo abs" style="left:608px;top:454px" role="img" aria-label="Photo of hands using a calculator over paperwork">
    <div class="photo-frame" style="left:30px;top:14px;right:14px;bottom:14px"></div>
  </div>
</section>

<section class="services" role="region" aria-label="Our services">
  <h2 class="sec-title abs">OUR SERVICES</h2>
  <p class="lead abs">Sed ut perspiciatis unde omnis iste natus error sit voluptatem accusantium doloremque laudantium totam rem aperiam</p>
  <div class="svc abs" style="left:89px;top:186px" role="img" aria-label="Working capital background photo"><h4>WORKING CAPITAL</h4><p>At vero eos et accusamus et iusto odio dignissimos ducimus qui blanditiis praesentium voluptatum</p></div>
  <div class="svc abs" style="left:437px;top:186px" role="img" aria-label="Debt consolidations background photo"><h4>DEBT CONSOLIDATIONS</h4><p>At vero eos et accusamus et iusto odio dignissimos ducimus qui blanditiis praesentium voluptatum</p></div>
  <div class="svc abs" style="left:786px;top:186px" role="img" aria-label="Payroll background photo"><h4>PAYROLL</h4><p>At vero eos et accusamus et iusto odio dignissimos ducimus qui blanditiis praesentium voluptatum</p></div>
  <div class="svc abs" style="left:89px;top:498px" role="img" aria-label="Operating expenses background photo"><h4>OPERATING EXPENSES</h4><p>At vero eos et accusamus et iusto odio dignissimos ducimus qui blanditiis praesentium voluptatum</p></div>
  <div class="svc abs" style="left:437px;top:498px" role="img" aria-label="Inventory background photo"><h4>INVENTORY</h4><p>At vero eos et accusamus et iusto odio dignissimos ducimus qui blanditiis praesentium voluptatum</p></div>
  <div class="svc abs" style="left:786px;top:498px" role="img" aria-label="Equipment financing background photo"><h4>EQUIPMENT FINANCING</h4><p>At vero eos et accusamus et iusto odio dignissimos ducimus qui blanditiis praesentium voluptatum</p></div>
  <div class="btn abs"><svg width="18" height="12" viewBox="0 0 24 16"><ellipse cx="12" cy="8" rx="11" ry="7" fill="#fff"/><circle cx="12" cy="8" r="3.5" fill="#2a2c30"/></svg>VIEW MORE</div>
</section>

<section class="team">
  <h2 class="sec-title abs">MEET OUR TEAM</h2>
  <svg class="arrow abs" style="left:33px" viewBox="0 0 34 34"><path d="M20 10l-7 7 7 7" fill="none" stroke="#555" stroke-width="2"/></svg>
  <svg class="arrow abs" style="left:1131px" viewBox="0 0 34 34"><path d="M14 10l7 7-7 7" fill="none" stroke="#555" stroke-width="2"/></svg>
  <div class="member abs" style="left:149px">
    <div class="portrait" style="left:0" role="img" aria-label="Headshot of the president and CEO"></div>
    <div class="bio" style="left:243px">
      <h3>Daniel<br>Whitcombe</h3>
      <h5>President &amp; CEO</h5>
      <p>Sed ut perspiciatis unde omnis iste natus error sit voluptatem accusantium</p>
      <div class="icons"><i></i><i></i><i></i></div>
    </div>
  </div>
  <div class="member abs" style="left:610px">
    <div class="bio" style="left:32px">
      <h3>Marcus<br>Ellery</h3>
      <h5>Executive Managing Director</h5>
      <p>Sed ut perspiciatis unde omnis iste natus error sit voluptatem accusantium</p>
      <div class="icons"><i></i><i></i><i></i></div>
    </div>
    <div class="portrait" style="left:228px" role="img" aria-label="Photo of the executive managing director seated"></div>
  </div>
</section>

<section class="video" role="img" aria-label="Background photo of a business team meeting in an office">
  <svg class="play abs" width="52" height="52" viewBox="0 0 52 52"><circle cx="26" cy="26" r="24" fill="none" stroke="#fff" stroke-width="3"/><path d="M21 16l15 10-15 10z" fill="#fff"/></svg>
  <div class="label abs">See Video</div>
  <h2 class="abs">COMPREHENSIVE VIDEO OF OUR SERVICES</h2>
  <p class="abs">Eum cu tantas legere complectitur, hinc utamur ea eam. Eum patrioque mnesarchum eu, diam erant convenire et vis. Et essent evertitur sea, vis cu ubique referrentur, sed eu dicant expetendis.</p>
</section>

<footer class="footer">
  <div class="brand abs">CORVANE<small>LENDING PARTNERS</small></div>
  <div class="f-social abs"><i></i><i></i><i></i><i></i></div>
  <div class="abs" style="left:343px;top:66px">
    <h4>Contact Us</h4>
    <div class="contact-list">
      <div><svg width="14" height="18" viewBox="0 0 14 18"><path d="M7 1a6 6 0 00-6 6c0 4.5 6 10 6 10s6-5.5 6-10a6 6 0 00-6-6z" fill="none" stroke="#fff" stroke-width="1.5"/><circle cx="7" cy="7" r="2" fill="#fff"/></svg><span>48 Harlow Street<br>#04-020 Harlow Court<br>US 50217</span></div>
      <div><svg width="14" height="14" viewBox="0 0 24 24"><path fill="#fff" d="M6.6 10.8a15 15 0 006.6 6.6l2.2-2.2c.3-.3.7-.4 1-.2 1.1.4 2.3.6 3.6.6.6 0 1 .4 1 1V20c0 .6-.4 1-1 1A17 17 0 013 4c0-.6.4-1 1-1h3.5c.6 0 1 .4 1 1 0 1.3.2 2.5.6 3.6.1.3 0 .7-.2 1z"/></svg><span>Phone (888-888-8888)</span></div>
      <div><svg width="16" height="14" viewBox="0 0 16 14"><rect x="1" y="4" width="14" height="9" fill="none" stroke="#fff" stroke-width="1.5"/><rect x="4" y="1" width="8" height="4" fill="#fff"/></svg><span>Fax (888-888-8888)</span></div>
      <div><svg width="16" height="12" viewBox="0 0 24 18"><rect x="1" y="1" width="22" height="16" fill="none" stroke="#fff" stroke-width="2"/><path d="M1 1l11 9 11-9" fill="none" stroke="#fff" stroke-width="2"/></svg><span>info@corvane.com</span></div>
    </div>
  </div>
  <div class="abs" style="left:645px;top:66px">
    <h4>Quick Links</h4>
    <ul><li>Home</li><li>About Us</li><li>Loan Programs</li><li>Loan Criteria</li><li>News</li><li>Apply Now</li><li>Contact</li></ul>
  </div>
  <div class="abs" style="left:925px;top:66px">
    <h4>Other Links</h4>
    <ul><li>FAQ</li><li>Feed Back</li><li>Terms and Conditions</li><li>Privacy Policy</li></ul>
  </div>
</footer>
<div class="copyright abs" style="left:0;width:1200px">Copyrights © 2018 | All Rights Reserved | Disclaimer</div>

</body>
</html>
```